Talon Microsystems PowerPoint Master Slide Deck Design

This is a 2-phase project to design a slide deck for a semiconductor company in the Silicon Valley. The design budget will be increased with each phase.
The slide deck will need to have one version with a dark background for presentations and a second version with a white background. Otherwise, the slides will be the same. I anticipate we will need a total of 10 slides, but that number may change.
The first phase will be to design a Title and a Title and Content slide.
- The Title Slide is the first slide of the deck. It should include the presentation title, the presenter's name and date of presentation
- The Title and Content slide should include a title and content with bullet points and up to 2 additional sub-bullets
- The Title and Content slide should have a footer that includes the slide #, Talon Microsystems Confidential, and the logo. This footer will be on every slide except the Title Slide
The first two slides will serve as the format for the remaining ~8 slides:
-Header and Content Text (1, 2, 4 column)
-Header and Content Image (bar chart, pie chart, tables)
-Break
-Title only
-Closing (Talon logo only)
Our slides contain a lot of content so a clean and simple design is best.
Both phases will need to include pre-set color options for
-Text and Lines
-Shadows
-Bullets and sub-bullets (including shapes, ex. circle, slash, square, etc.)
-Bar charts, pie charts, tables
Samples of our collateral are attached. Logo files are also attached
Look and feel
Each slider illustrates characteristics of the customer's brand and the style your logo design should communicate.

```html
<!DOCTYPE html>
<html lang="en">
<head>
<meta charset="utf-8">
<title>Talon Microsystems Slide Deck</title>
<link href="https://fonts.googleapis.com/css2?family=Montserrat:wght@400;500;600;700;800&display=swap" rel="stylesheet">
<style>
  :root {
    --canvas: #b3b3b3;
    --white: #ffffff;
    --ink: #2b2b2b;
    --body: #555a63;
    --blue-deep: #0b2ff0;
    --blue: #1a3ce8;
    --blue-bright: #1570f0;
    --cyan: #12b4f2;
    --purple: #6a3cbc;
    --red: #ee3a5a;
    --orange: #fb9f0b;
    --gold: #f2a516;
  }
  * { box-sizing: border-box; margin: 0; padding: 0; }
  html, body { width: 1200px; height: 1072px; overflow: hidden; }
  body { background: var(--canvas); font-family: "Montserrat", sans-serif; position: relative; }

  .slide { position: absolute; width: 543px; height: 306px; background: var(--white); overflow: hidden; }
  .slide--title { left: 38px; top: 45px; }
  .slide--break { left: 617px; top: 45px; }
  .slide--list { left: 38px; top: 380px; }
  .slide--section { left: 617px; top: 380px; }
  .slide--chart { left: 38px; top: 720px; }
  .slide--closing { left: 617px; top: 720px; }

  /* brand name */
  .brand { position: absolute; display: flex; align-items: center; gap: 5px; }
  .brand__dot { width: 11px; height: 11px; border-radius: 50%; background: var(--blue); }
  .brand__name { font-weight: 600; font-size: 15px; color: var(--ink); letter-spacing: 0.5px; }
  .slide--break .brand, .slide--list .brand, .slide--chart .brand { left: 23px; top: 16px; }

  /* footer */
  .footer { position: absolute; left: 0; right: 0; bottom: 0; height: 21px;
    background: linear-gradient(90deg, var(--blue-deep), var(--blue-bright) 55%, var(--cyan)); }
  .footer__brand { position: absolute; left: 27px; top: 5px; font-size: 7.5px; font-weight: 600; color: var(--white); letter-spacing: 0.3px; display: flex; align-items: center; gap: 3px; }
  .footer__brand i { width: 6px; height: 6px; border-radius: 50%; background: var(--white); display: block; }
  .footer__label { position: absolute; left: 0; right: 0; top: 7px; text-align: center; font-size: 5.6px; color: var(--white); letter-spacing: 0.2px; }
  .footer__page { position: absolute; right: 15px; top: 3.5px; width: 14px; height: 14px; border-radius: 50%; background: var(--blue-deep); color: var(--white); font-size: 5.5px; font-weight: 700; display: flex; align-items: center; justify-content: center; }

  .slide-heading { position: absolute; right: 28px; top: 19px; font-size: 16.5px; font-weight: 700; color: var(--ink); letter-spacing: 0.3px; }

  .body-copy { position: absolute; font-size: 6.4px; line-height: 9.9px; color: var(--body); text-align: justify; }
  .body-copy p + p { margin-top: 9.9px; }

  /* title slide */
  .slide--title { background: linear-gradient(120deg, #0a35e6 0%, #1f6cf0 55%, #12a8ef 100%); }
  .slide--title .hero { position: absolute; inset: 0; }
  .title-brand { position: absolute; left: 0; right: 0; top: 104px; display: flex; justify-content: center; align-items: center; gap: 10px; }
  .title-brand .brand__dot { width: 26px; height: 26px; background: var(--white); }
  .title-brand .brand__name { font-size: 36px; color: var(--white); font-weight: 500; }
  .title-main { position: absolute; left: 0; right: 0; top: 166px; text-align: center; font-size: 22px; font-weight: 700; color: var(--white); letter-spacing: 0.3px; }
  .title-presenter { position: absolute; left: 0; right: 0; top: 205px; text-align: center; font-size: 8.5px; font-weight: 700; color: var(--white); }
  .title-date { position: absolute; left: 233px; top: 223px; width: 77px; height: 19px; background: var(--blue-deep); color: var(--white); font-size: 8px; font-weight: 700; display: flex; align-items: center; justify-content: center; }

  /* break slide */
  .break-ring { position: absolute; left: 315px; top: 62px; width: 346px; height: 346px; border-radius: 50%; background: linear-gradient(160deg, var(--blue-deep), var(--cyan)); }
  .break-photo { position: absolute; left: 316px; top: 85px; width: 320px; height: 320px; border-radius: 50%; background: radial-gradient(circle at 55% 40%, #cfe6fb 0%, #6fb4ee 35%, #2e6fd4 70%, #1a3f9a 100%); }
  .slide--break .footer { z-index: 2; }

  /* list slide */
  .list-item { position: absolute; display: flex; gap: 0; }
  .list-item__num { width: 34px; font-size: 19px; font-weight: 700; color: var(--blue); line-height: 1; margin-top: 1px; }
  .list-item__text { width: 200px; font-size: 6.4px; line-height: 10px; color: var(--body); }

  /* section slide */
  .slide--section .brand { left: 0; right: 0; top: 15px; justify-content: center; }
  .section-image { position: absolute; left: 0; top: 57px; width: 543px; height: 228px;
    background: radial-gradient(ellipse at 50% 55%, #3a6cff 0%, #1d3fd6 45%, #0e22a6 100%); }
  .section-title { position: absolute; left: 0; right: 0; top: 157px; text-align: center; font-size: 24px; font-weight: 800; color: var(--white); letter-spacing: 0.5px; }

  /* chart slide */
  .donut { position: absolute; left: 22px; top: 47px; }
  .donut-label { font-family: "Montserrat", sans-serif; fill: var(--white); }

  /* closing slide */
  .closing-brand { position: absolute; left: 0; right: 0; top: 132px; display: flex; justify-content: center; align-items: center; gap: 14px; }
  .closing-brand .brand__dot { width: 34px; height: 34px; background: var(--blue); }
  .closing-brand .brand__name { font-size: 46px; font-weight: 600; color: var(--ink); }
</style>
</head>
<body>

<!-- Title slide -->
<section class="slide slide--title">
  <div class="hero" role="img" aria-label="Blue-toned close-up of a circuit board"></div>
  <div class="title-brand"><span class="brand__dot"></span><span class="brand__name">Talon</span></div>
  <h1 class="title-main">TALON MICROSYSTEMS</h1>
  <p class="title-presenter">JOHN DOE</p>
  <p class="title-date">DEC 20,2023</p>
</section>

<!-- Break slide -->
<section class="slide slide--break">
  <div class="brand"><span class="brand__dot"></span><span class="brand__name">Talon</span></div>
  <h2 class="slide-heading">BREAK</h2>
  <div class="body-copy" style="left:22px; top:64px; width:256px;">
    <p>Lorem ipsum dolor sit amet, consectetur adipiscing elit, sed do eiusmod tempor incididunt ut labore et dolore magna aliqua. Ut enim ad minim veniam, quis nostrud exercitation ullamco laboris nisi ut aliquip ex ea commodo consequat. Duis aute irure dolor in reprehenderit in voluptate velit esse cillum dolore eu fugiat nulla pariatur. Excepteur sint occaecat cupidatat non proident, sunt in culpa qui officia deserunt mollit anim id est laborum.</p>
    <p>Sed ut perspiciatis unde omnis iste natus error sit voluptatem accusantium doloremque laudantium, totam rem aperiam, eaque ipsa quae ab illo inventore veritatis et quasi architecto beatae vitae dicta sunt explicabo. Nemo enim ipsam voluptatem quia voluptas sit aspernatur aut odit aut fugit, sed quia consequuntur magni dolores eos qui ratione voluptatem sequi nesciunt. Neque porro quisquam est, qui dolorem ipsum quia dolor sit amet, consectetur, adipisci velit, sed quia non numquam eius modi tempora incidunt ut labore et dolore magnam aliquam quaerat voluptatem. Ut enim ad minima veniam, quis nostrum exercitationem ullam corporis suscipit laboriosam, nisi ut aliquid ex ea commodi consequatur? Quis autem vel eum iure reprehenderit qui in ea voluptate velit esse quam nihil molestiae consequatur, vel illum qui dolorem eum fugiat quo voluptas nulla pariatur</p>
  </div>
  <div class="break-ring"></div>
  <div class="break-photo" role="img" aria-label="Gloved hand holding a microchip in a cleanroom"></div>
  <footer class="footer">
    <span class="footer__brand"><i></i>Talon</span>
    <span class="footer__label">TALON MICROSYSTEMS CONFIDENTIAL</span>
    <span class="footer__page">04</span>
  </footer>
</section>

<!-- Numbered list slide -->
<section class="slide slide--list">
  <div class="brand"><span class="brand__dot"></span><span class="brand__name">Talon</span></div>
  <h2 class="slide-heading">TITLE HERE</h2>
  <div class="list-item" style="left:25px; top:65px;"><span class="list-item__num">01</span><p class="list-item__text">Lorem ipsum dolor sit amet, consectetur adipiscing elit, sed do tempor incididunt ut labore et dolore magna aliqua.</p></div>
  <div class="list-item" style="left:25px; top:110px;"><span class="list-item__num">02</span><p class="list-item__text">Lorem ipsum dolor sit amet, consectetur adipiscing elit, sed do tempor incididunt ut labore et dolore magna aliqua.</p></div>
  <div class="list-item" style="left:25px; top:155px;"><span class="list-item__num">03</span><p class="list-item__text">Lorem ipsum dolor sit amet, consectetur adipiscing elit, sed do tempor incididunt ut labore et dolore magna aliqua.</p></div>
  <div class="list-item" style="left:25px; top:200px;"><span class="list-item__num">04</span><p class="list-item__text">Lorem ipsum dolor sit amet, consectetur adipiscing elit, sed do tempor incididunt ut labore et dolore magna aliqua.</p></div>
  <div class="list-item" style="left:25px; top:246px;"><span class="list-item__num">05</span><p class="list-item__text">Lorem ipsum dolor sit amet, consectetur adipiscing elit, sed do tempor incididunt ut labore et dolore magna aliqua.</p></div>
  <div class="list-item" style="left:288px; top:65px;"><span class="list-item__num">06</span><p class="list-item__text">Lorem ipsum dolor sit amet, consectetur adipiscing elit, sed do tempor incididunt ut labore et dolore magna aliqua.</p></div>
  <div class="list-item" style="left:288px; top:110px;"><span class="list-item__num">07</span><p class="list-item__text">Lorem ipsum dolor sit amet, consectetur adipiscing elit, sed do tempor incididunt ut labore et dolore magna aliqua.</p></div>
  <div class="list-item" style="left:288px; top:155px;"><span class="list-item__num">08</span><p class="list-item__text">Lorem ipsum dolor sit amet, consectetur adipiscing elit, sed do tempor incididunt ut labore et dolore magna aliqua.</p></div>
  <div class="list-item" style="left:288px; top:200px;"><span class="list-item__num">09</span><p class="list-item__text">Lorem ipsum dolor sit amet, consectetur adipiscing elit, sed do tempor incididunt ut labore et dolore magna aliqua.</p></div>
  <div class="list-item" style="left:288px; top:246px;"><span class="list-item__num">10</span><p class="list-item__text">Lorem ipsum dolor sit amet, consectetur adipiscing elit, sed do tempor incididunt ut labore et dolore magna aliqua.</p></div>
  <footer class="footer">
    <span class="footer__brand"><i></i>Talon</span>
    <span class="footer__label">TALON MICROSYSTEMS CONFIDENTIAL</span>
    <span class="footer__page">02</span>
  </footer>
</section>

<!-- Section title slide -->
<section class="slide slide--section">
  <div class="brand"><span class="brand__dot"></span><span class="brand__name">Talon</span></div>
  <div class="section-image" role="img" aria-label="Glowing blue chip on a circuit board"></div>
  <h2 class="section-title">TITLE HERE</h2>
  <footer class="footer">
    <span class="footer__brand"><i></i>Talon</span>
    <span class="footer__label">TALON MICROSYSTEMS CONFIDENTIAL</span>
    <span class="footer__page">05</span>
  </footer>
</section>

<!-- Chart slide -->
<section class="slide slide--chart">
  <div class="brand"><span class="brand__dot"></span><span class="brand__name">Talon</span></div>
  <h2 class="slide-heading">TITLE HERE</h2>
  <svg class="donut" width="212" height="212" viewBox="-106 -106 212 212">
    <!-- red 40%: 20° to 164° -->
    <path d="M35.9 -98.7 A105 105 0 0 1 28.9 100.9 L15.4 53.8 A56 56 0 0 0 19.2 -52.6 Z" fill="var(--red)"/>
    <!-- orange 30%: 164° to 272° -->
    <path d="M28.9 100.9 A105 105 0 0 1 -104.9 3.7 L-56 2 A56 56 0 0 0 15.4 53.8 Z" fill="var(--orange)"/>
    <!-- purple 30%: 272° to 380° -->
    <path d="M-104.9 3.7 A105 105 0 0 1 35.9 -98.7 L19.2 -52.6 A56 56 0 0 0 -56 2 Z" fill="var(--purple)"/>
    <circle r="56" fill="var(--white)"/>
    <text class="donut-label" x="3" y="-75" text-anchor="middle" font-size="6.5" font-weight="700">DATA</text>
    <text class="donut-label" x="3" y="-57" text-anchor="middle" font-size="18" font-weight="800">30%</text>
    <text class="donut-label" x="-71" y="18" text-anchor="middle" font-size="6.5" font-weight="700">DATA</text>
    <text class="donut-label" x="-71" y="36" text-anchor="middle" font-size="18" font-weight="800">30%</text>
    <text class="donut-label" x="49" y="56" text-anchor="middle" font-size="6.5" font-weight="700">DATA</text>
    <text class="donut-label" x="49" y="74" text-anchor="middle" font-size="18" font-weight="800">40%</text>
    <text x="2" y="-24" text-anchor="middle" font-family="Montserrat, sans-serif" font-size="8" font-weight="600" fill="var(--gold)">LOREM IPSUM</text>
    <g fill="var(--gold)">
      <circle cx="-20" cy="-15" r="0.8"/><circle cx="-15" cy="-15" r="0.9"/><circle cx="-10" cy="-15" r="1"/><circle cx="-5" cy="-15" r="1.2"/><circle cx="0" cy="-15" r="1.3"/><circle cx="5" cy="-15" r="1.2"/><circle cx="10" cy="-15" r="1"/><circle cx="15" cy="-15" r="0.9"/><circle cx="20" cy="-15" r="0.8"/><circle cx="25" cy="-15" r="0.7"/>
    </g>
    <g font-family="Montserrat, sans-serif" font-size="6.2" fill="var(--body)" text-anchor="middle">
      <text x="2" y="0">Lorem ipsum dolor sit</text>
      <text x="2" y="9.5">amet, consectetuer</text>
      <text x="2" y="19">adipiscing elit, sed diam</text>
      <text x="2" y="28.5">nonummy nibh euismod</text>
      <text x="2" y="38">tincidunt.</text>
    </g>
  </svg>
  <div class="body-copy" style="left:259px; top:54px; width:256px; text-align:justify; text-align-last:right;">
    <p>Lorem ipsum dolor sit amet, consectetur adipiscing elit, sed do eiusmod tempor incididunt ut labore et dolore magna aliqua. Ut enim ad minim veniam, quis nostrud exercitation ullamco laboris nisi ut aliquip ex ea commodo consequat. Duis aute irure dolor in reprehenderit in voluptate velit esse cillum dolore eu fugiat nulla pariatur. Excepteur sint occaecat cupidatat non proident, sunt in culpa qui officia deserunt mollit anim id est laborum.</p>
    <p>Sed ut perspiciatis unde omnis iste natus error sit voluptatem accusantium doloremque laudantium, totam rem aperiam, eaque ipsa quae ab illo inventore veritatis et quasi architecto beatae vitae dicta sunt explicabo. Nemo enim ipsam voluptatem quia voluptas sit aspernatur aut odit aut fugit, sed quia consequuntur magni dolores eos qui ratione voluptatem sequi nesciunt. Neque porro quisquam est, qui dolorem ipsum quia dolor sit amet, consectetur, adipisci velit, sed quia non numquam eius modi tempora incidunt ut labore et dolore magnam aliquam quaerat voluptatem. Ut enim ad minima veniam, quis nostrum exercitationem ullam corporis suscipit laboriosam, nisi ut aliquid ex ea commodi consequatur? Quis autem vel eum iure reprehenderit qui in ea voluptate velit esse quam nihil molestiae consequatur, vel illum qui dolorem eum fugiat quo voluptas nulla pariatur</p>
  </div>
  <footer class="footer">
    <span class="footer__brand"><i></i>Talon</span>
    <span class="footer__label">TALON MICROSYSTEMS CONFIDENTIAL</span>
    <span class="footer__page">03</span>
  </footer>
</section>

<!-- Closing slide -->
<section class="slide slide--closing">
  <div class="closing-brand"><span class="brand__dot"></span><span class="brand__name">Talon</span></div>
  <footer class="footer">
    <span class="footer__brand"><i></i>Talon</span>
    <span class="footer__label">TALON MICROSYSTEMS CONFIDENTIAL</span>
    <span class="footer__page">06</span>
  </footer>
</section>

</body>
</html>
```